Medical Billing Company Needs a Business Card Design

We need a business card design for a Florida based medical billing company called 'Clinicians Keystone Solutions'. We specialize in providing revenue cycle management services to physician and therapist offices (we're basically their back-office processing partner for providing billing software, claims submissions, A/R follow-up and patient statements & collections. Our logo is red and blue-ish, so make sure that whatever other elements are used will match appropriately. Our current business card design has a too small font size. I'd like to project an image that shows we are modern & reliable. On a side note, I'm planning on using ZUB for printing these cards.

Target Market(s)

Office managers, physicians, therapists

Industry/Entity Type

Printing

Requirements
Must have
• Logo
Name of Employee
Phone
Fax
E-mail
Website

```html
<!DOCTYPE html>
<html lang="en">
<head>
<meta charset="utf-8">
<title>Clinicians Keystone Solutions – Business Card</title>
<link rel="stylesheet" href="https://fonts.googleapis.com/css2?family=Open+Sans:wght@400;600;700&display=swap">
<style>
  :root {
    --navy: #241a6e;
    --indigo: #2c1f7a;
    --violet: #5a4a9e;
    --red: #a3141c;
    --ink: #3a3a44;
    --rule: #9a9aa6;
    --paper: #ffffff;
    --backdrop: #e9e7ee;
  }
  * { box-sizing: border-box; margin: 0; padding: 0; }
  html, body {
    width: 1200px; height: 720px; overflow: hidden;
    background: var(--backdrop);
    font-family: "Open Sans", Arial, sans-serif;
  }
  .canvas {
    width: 1200px; height: 720px;
    display: flex; align-items: center; justify-content: center; gap: 40px;
  }
  .card {
    position: relative;
    width: 540px; height: 309px;
    border-radius: 4px;
    overflow: hidden;
    box-shadow: 0 6px 18px rgba(30, 20, 80, 0.18);
  }

  /* Front */
  .card-front { background: var(--paper); }
  .accent-band {
    position: absolute; top: 0; right: 0;
    width: 308px; height: 64px;
    background: linear-gradient(90deg, var(--red) 0%, var(--indigo) 55%, var(--navy) 100%);
  }
  .holder {
    position: absolute; top: 10px; right: 20px;
    text-align: right; color: #fff;
  }
  .holder-name { font-weight: 700; font-size: 19px; line-height: 1.15; }
  .holder-title { font-size: 13px; line-height: 1.3; }
  .brand {
    position: absolute; left: 34px; top: 134px;
    display: flex; align-items: center; gap: 10px;
  }
  .brand-mark { width: 14px; height: 14px; background: var(--red); }
  .brand-name {
    color: var(--navy); font-weight: 600; font-size: 21px;
    letter-spacing: 2.5px; text-transform: uppercase;
  }
  .contact {
    position: absolute; left: 34px; top: 208px;
    list-style: none; font-size: 13.5px; color: var(--ink);
  }
  .contact li { display: flex; align-items: center; gap: 8px; line-height: 19px; }
  .contact svg { width: 11px; height: 11px; fill: var(--navy); flex: none; }
  .address {
    position: absolute; left: 298px; top: 186px;
    padding-left: 12px; border-left: 1px solid var(--rule);
    font-size: 13.5px; line-height: 18px; color: var(--ink);
    font-style: normal;
  }

  /* Back */
  .card-back {
    background: linear-gradient(120deg, var(--violet) 0%, var(--indigo) 60%, var(--navy) 100%);
    color: #fff;
  }
  .back-brand {
    position: absolute; left: 0; right: 0; top: 104px;
    display: flex; align-items: center; justify-content: center; gap: 12px;
  }
  .back-brand .brand-mark { width: 18px; height: 18px; background: #fff; }
  .back-brand .brand-name { color: #fff; font-size: 24px; }
  .back-web {
    position: absolute; left: 0; right: 0; bottom: 62px;
    text-align: center; font-size: 15px; letter-spacing: 3.5px;
  }
</style>
</head>
<body>
<main class="canvas">
  <section class="card card-front" aria-label="Card front">
    <div class="accent-band" role="img" aria-label="Decorative navy and red accent ribbon"></div>
    <div class="holder">
      <div class="holder-name">Your Name</div>
      <div class="holder-title">Title</div>
    </div>
    <div class="brand">
      <span class="brand-name">Clinicians Keystone</span>
      <span class="brand-mark" aria-hidden="true"></span>
    </div>
    <ul class="contact">
      <li><svg viewBox="0 0 12 12" aria-hidden="true"><path d="M2.5 1l2 2-1 1.3a6 6 0 0 0 4.2 4.2L9 7.5l2 2-1.3 1.5C5.5 11 1 6.5 1 2.3z"/></svg>123-456-0789</li>
      <li><svg viewBox="0 0 12 12" aria-hidden="true"><rect x="3" y="0.5" width="6" height="11" rx="1"/><rect x="4" y="2" width="4" height="6" fill="#fff"/></svg>123-456-0789</li>
      <li><svg viewBox="0 0 12 12" aria-hidden="true"><path d="M0.5 2.5h11v7h-11z"/><path d="M0.5 2.5L6 7l5.5-4.5" fill="none" stroke="#fff" stroke-width="1"/></svg>info@clinicianskeystone.com</li>
      <li><svg viewBox="0 0 12 12" aria-hidden="true"><circle cx="6" cy="6" r="5.5"/><path d="M0.5 6h11M6 0.5v11M6 0.5c-3 3-3 8 0 11M6 0.5c3 3 3 8 0 11" fill="none" stroke="#fff" stroke-width="0.8"/></svg>www.clinicianskeystone.com</li>
    </ul>
    <address class="address">
      Street Name, City Name<br>State Zip Code
    </address>
  </section>

  <section class="card card-back" aria-label="Card back">
    <div class="back-brand">
      <span class="brand-mark" aria-hidden="true"></span>
      <span class="brand-name">Clinicians Keystone</span>
    </div>
    <div class="back-web">www.clinicianskeystone.com</div>
  </section>
</main>
</body>
</html>
```